Communication and Marketing agency needs a new presentation card

We are a group of communication and marketing agencies specialized in companies that are in the logistics and industrial sector. The head agency is TELVANO Grupo and the group consists of 4 agencies: TELVANO Media, TELVANO Digital, TELVANO Research and DifundeEnPantalla. We hace 4 offices in Spain (Madrid, Barcelona, Valencia and Murcia). We are looking for a clean and attractive design that transmits our experience, brand presence in the market and knowledge to those who receive the card.It has to maintain the colors of the logo that is attached.
Target Market(s)
logistics and industrial sector
Marketing department
Contact Information for Business Card
Clean and attractive design

```html
<!DOCTYPE html>
<html lang="en">
<head>
<meta charset="utf-8">
<title>TELVANO Grupo – Business Card</title>
<link rel="stylesheet" href="https://fonts.googleapis.com/css2?family=Open+Sans:wght@300;400;700&display=swap">
<style>
  :root {
    --backdrop: #a61f23;
    --card-dark: #1b1b1b;
    --map-tone-a: #262626;
    --map-tone-b: #1d1d1d;
    --card-light: #fafafa;
    --brand-red: #b01c2a;
    --brand-grey: #5e5e5e;
    --accent-orange: #e0834c;
    --ink: #2a2a2a;
  }
  * { box-sizing: border-box; margin: 0; padding: 0; }
  html, body {
    width: 1200px; height: 1200px; overflow: hidden;
    background: var(--backdrop);
    font-family: "Open Sans", Arial, sans-serif;
  }
  .canvas { position: relative; width: 1200px; height: 1200px; }

  .card {
    position: absolute; left: 223px; width: 815px; height: 466px;
    overflow: hidden;
  }
  .card--front { top: 76px; background: var(--card-dark); }
  .card--back  { top: 658px; background: var(--card-light); }

  .world-map {
    position: absolute; left: 20px; top: 20px; width: 775px; height: 426px;
    background: radial-gradient(ellipse at 55% 40%, var(--map-tone-a) 0%, var(--map-tone-b) 70%, transparent 100%);
    opacity: .9;
  }

  .wordmark {
    position: absolute; font-weight: 300; text-align: right; line-height: 1;
  }
  .wordmark--front {
    right: 152px; top: 150px; color: var(--brand-grey);
  }
  .wordmark--front .wordmark__name { font-size: 92px; letter-spacing: 4px; display: block; }
  .wordmark--front .wordmark__unit { font-size: 56px; display: block; margin-top: 12px; }

  .wordmark--back {
    left: 53px; top: 168px; width: 338px; color: var(--brand-red);
  }
  .wordmark--back .wordmark__name { font-size: 60px; letter-spacing: 2px; display: block; }
  .wordmark--back .wordmark__unit { font-size: 40px; display: block; margin-top: 8px; }

  .divider {
    position: absolute; left: 423px; top: 138px; width: 2px; height: 182px;
    background: var(--accent-orange);
  }

  .contact {
    position: absolute; left: 461px; top: 134px; color: var(--ink);
  }
  .contact__name { font-size: 31px; font-weight: 700; line-height: 1.1; }
  .contact__role { font-size: 19px; color: var(--accent-orange); line-height: 1.2; }
  .contact__address { font-size: 19px; line-height: 1.25; margin-top: 4px; }
  .contact__list { list-style: none; margin-top: 12px; }
  .contact__item { display: flex; align-items: center; font-size: 19px; line-height: 1.25; }
  .contact__icon { width: 16px; height: 16px; margin-right: 9px; flex: none; }
</style>
</head>
<body>
<main class="canvas">

  <section class="card card--front" aria-label="Card front">
    <div class="world-map" role="img" aria-label="Faint dotted world map in dark grey"></div>
    <div class="wordmark wordmark--front">
      <span class="wordmark__name">TELVANO</span>
      <span class="wordmark__unit">Digital</span>
    </div>
  </section>

  <section class="card card--back" aria-label="Card back">
    <div class="wordmark wordmark--back">
      <span class="wordmark__name">TELVANO</span>
      <span class="wordmark__unit">Grupo</span>
    </div>

    <div class="divider"></div>

    <div class="contact">
      <p class="contact__name">Mark Delaney</p>
      <p class="contact__role">Manager</p>
      <p class="contact__address">#210 – 4471 38TH Avenue NW<br>Calverton AB T4R 2K7 CANADA</p>
      <ul class="contact__list">
        <li class="contact__item">
          <svg class="contact__icon" viewBox="0 0 16 16" aria-hidden="true">
            <path d="M4 1.5 L6.5 1.5 L7 5 L5.3 6.2 Q6.5 9.5 9.8 10.7 L11 9 L14.5 9.5 L14.5 12 Q14.5 14.5 12 14.5 Q2 13.5 1.5 4 Q1.5 1.5 4 1.5 Z" fill="var(--accent-orange)"/>
          </svg>
          +587 -614- 2093
        </li>
        <li class="contact__item">
          <svg class="contact__icon" viewBox="0 0 16 16" aria-hidden="true">
            <rect x="1" y="3" width="14" height="10" fill="var(--accent-orange)"/>
            <path d="M1 3 L8 9 L15 3" fill="none" stroke="#fff" stroke-width="1.3"/>
          </svg>
          info@brightanvil.ca
        </li>
        <li class="contact__item">
          <svg class="contact__icon" viewBox="0 0 16 16" aria-hidden="true">
            <g fill="none" stroke="var(--accent-orange)" stroke-width="1.1">
              <circle cx="8" cy="8" r="6.5"/>
              <ellipse cx="8" cy="8" rx="3" ry="6.5"/>
              <line x1="1.5" y1="8" x2="14.5" y2="8"/>
              <line x1="2.5" y1="4.8" x2="13.5" y2="4.8"/>
              <line x1="2.5" y1="11.2" x2="13.5" y2="11.2"/>
            </g>
          </svg>
          www.brightanvil.ca
        </li>
      </ul>
    </div>
  </section>

</main>
</body>
</html>
```